Veltrane Group Business Card Design

The CEO is looking for a new trendy look for his business card.
You can stay with current branding or come up with something new/creative. It can be 3D, including Medical Office buildings. You can use our logo in a variety of colors. Please include name, title, company name, company website, email address, cell number

Target Market(s)

Real Estate Development and Construction

Industry/Entity Type

Health care real estate

Contact Information for Business Card

Rohesh Kamdar, CEO M-604.781.2249 E-roheshkamdar@veltrane.com Address:4180 Lindqvist Ave, Tampa, FL 33482 www.veltrane.com

Font styles to use
Other font styles liked:
• Be creative

Requirements
Must have
• Creative, trendy look
Nice to have
• Please go to our website to get a feel- www. veltrane.com
Should not have
• small fonts

```html
<!DOCTYPE html>
<html lang="en">
<head>
<meta charset="utf-8">
<title>Veltrane Group Business Card</title>
<link href="https://fonts.googleapis.com/css2?family=Poppins:wght@400;500;700;800&display=swap" rel="stylesheet">
<style>
  :root {
    --page: #e9e7e3;
    --navy: #1b2a44;
    --navy-deep: #15223a;
    --red: #a61b29;
    --red-bright: #d93049;
    --ink: #3a3d45;
    --rule: #8a93a6;
    --paper: #ffffff;
  }
  * { margin: 0; padding: 0; box-sizing: border-box; }
  html, body {
    width: 1200px; height: 900px; overflow: hidden;
    background: var(--page);
    font-family: "Poppins", sans-serif;
  }
  .canvas {
    position: relative; width: 1200px; height: 900px;
  }
  .card {
    position: absolute; left: 320px; width: 560px; height: 320px;
    box-shadow: 0 10px 28px rgba(0,0,0,0.18);
  }
  .card--front {
    top: 90px;
    background: linear-gradient(160deg, var(--navy) 0%, var(--navy-deep) 100%);
    display: flex; align-items: center; justify-content: center;
  }
  .card--back {
    top: 490px;
    background: var(--paper);
  }
  .brand {
    font-weight: 800; letter-spacing: -1px; line-height: 1;
    white-space: nowrap;
  }
  .card--front .brand { color: var(--red-bright); font-size: 52px; }
  .card--back .brand {
    position: absolute; top: 34px; right: 36px;
    color: var(--red); font-size: 38px;
  }
  .contact {
    position: absolute; left: 40px; bottom: 30px; width: 330px;
  }
  .contact__name {
    color: var(--red); font-weight: 800; font-size: 22px;
    text-transform: uppercase; letter-spacing: 0.3px; line-height: 1.1;
  }
  .contact__title {
    color: var(--ink); font-size: 16px; font-weight: 400; margin-bottom: 12px;
  }
  .contact__list { list-style: none; }
  .contact__item {
    display: flex; align-items: center; gap: 10px;
    color: var(--ink); font-size: 14px; line-height: 22px;
  }
  .contact__icon { width: 16px; height: 16px; flex: none; }
  .contact__rule {
    border: none; border-top: 1px solid var(--rule);
    margin: 10px 0 8px;
  }
  .contact__address { color: var(--ink); font-size: 14px; }
</style>
</head>
<body>
<main class="canvas">
  <section class="card card--front" aria-label="Card front">
    <p class="brand">Veltrane Group</p>
  </section>

  <section class="card card--back" aria-label="Card back">
    <p class="brand">Veltrane Group</p>
    <div class="contact">
      <h1 class="contact__name">Rohesh Kamdar</h1>
      <p class="contact__title">CEO</p>
      <ul class="contact__list">
        <li class="contact__item">
          <svg class="contact__icon" viewBox="0 0 16 16" aria-hidden="true">
            <rect x="4" y="1" width="8" height="14" rx="1.5" fill="none" stroke="#a61b29" stroke-width="1.5"/>
            <line x1="7" y1="12.5" x2="9" y2="12.5" stroke="#a61b29" stroke-width="1.2"/>
          </svg>
          604.781.2249
        </li>
        <li class="contact__item">
          <svg class="contact__icon" viewBox="0 0 16 16" aria-hidden="true">
            <rect x="1" y="3" width="14" height="10" fill="#a61b29"/>
            <polyline points="1,3 8,9 15,3" fill="none" stroke="#fff" stroke-width="1.3"/>
          </svg>
          roheshkamdar@veltrane.com
        </li>
        <li class="contact__item">
          <svg class="contact__icon" viewBox="0 0 16 16" aria-hidden="true">
            <g fill="none" stroke="#a61b29" stroke-width="1.2">
              <circle cx="8" cy="8" r="6.5"/>
              <ellipse cx="8" cy="8" rx="3" ry="6.5"/>
              <line x1="1.5" y1="8" x2="14.5" y2="8"/>
              <line x1="2.5" y1="4.5" x2="13.5" y2="4.5"/>
              <line x1="2.5" y1="11.5" x2="13.5" y2="11.5"/>
            </g>
          </svg>
          www.veltrane.com
        </li>
      </ul>
      <hr class="contact__rule">
      <p class="contact__address">4180 Lindqvist Ave, Tampa, FL 33482</p>
    </div>
  </section>
</main>
</body>
</html>
```